wine label for ultra premium vineyard in Bendigo, Central Otago, New Zealand

"WREN" is our new wine brand, with grapes grown in our spectacular "ter Hoeven" vineyard. The small, elevated vineyard overlooks a river valley and snowy mountains. We would like a highly elegant label for our 2018 pinot noir wine, which highlights the quality of wine and our very special vineyard location. "WREN" has to be prominent, with secondary emphasis on "ter Hoeven vineyard" and "Bendigo, Central Otago". A stylized WREN logo (bird) could be a useful design device instead of the commonly seen illustrated mountain landscape (which is quite common for our local wines). Label size 90 high, 110 wide. Please use a pinot noir / burgundy bottle. See here for vineyard pics, and also below pics for other local wine labels and pics for inspiration / styles. https://www.instagram.com/jan.ter.hoeven/

Target Market(s)

average bottle price for this premium red pinot noir would be aroundUS$40. target market are generally urban professionals aged 25 and older with a high degree of interest in pinot noir wine, and who are familiar with New Zealand pinot noir (ie. already know several brands).

Colors
ed252d

Requirements
Must have
• distinctive label, sophisticated look
Nice to have
• classy white paper stock
Should not have
• label must not get too busy... less but high quality and distinctive is more....

```html
<!DOCTYPE html>
<html lang="en">
<head>
<meta charset="utf-8">
<title>WREN Pinot Noir 2018 – Wine Label</title>
<link rel="stylesheet" href="https://fonts.googleapis.com/css2?family=Bodoni+Moda:opsz,wght@6..96,400&family=Forum&family=Nanum+Pen+Script&display=swap">
<style>
  :root {
    --backdrop: #181617;
    --paper: #ecebe7;
    --wine-red: #ed252d;
    --feather-rose: #d9646c;
    --bird-orange: #e4661a;
    --bird-grey: #959bb2;
    --rule: 2.5px;
  }
  * { margin: 0; padding: 0; box-sizing: border-box; }
  html, body {
    width: 1200px;
    height: 1200px;
    overflow: hidden;
    background: var(--backdrop);
  }
  .label {
    position: absolute;
    left: 191px;
    top: 265px;
    width: 817px;
    height: 669px;
    background: var(--paper);
    color: var(--wine-red);
    overflow: hidden;
  }
  .rule { position: absolute; background: var(--wine-red); }
  .rule--vintage-divider { left: 638px; top: 0; width: var(--rule); height: 572px; }
  .rule--box-top { left: 237px; top: 261px; width: 580px; height: var(--rule); }
  .rule--box-left { left: 237px; top: 261px; width: var(--rule); height: 408px; }
  .rule--box-bottom { left: 0; top: 570px; width: 640px; height: var(--rule); }

  .brand-name {
    position: absolute;
    left: 100px;
    top: 56px;
    width: 320px;
    font-family: "Bodoni Moda", serif;
    font-weight: 400;
    font-size: 118px;
    line-height: 1;
    letter-spacing: 2px;
    text-align: center;
  }
  .vintage {
    position: absolute;
    left: 655px;
    top: 108px;
    width: 145px;
    text-align: center;
    font-family: "Bodoni Moda", serif;
    font-size: 29px;
    line-height: 1;
  }
  .varietal, .region {
    position: absolute;
    font-family: "Forum", serif;
    font-size: 28px;
    line-height: 1;
    letter-spacing: 0.3px;
    white-space: nowrap;
  }
  .varietal { left: 33px; top: 452px; }
  .region { left: 257px; top: 611px; }

  .vineyard-name {
    position: absolute;
    left: 676px;
    top: 286px;
    height: 270px;
    writing-mode: vertical-rl;
    font-family: "Nanum Pen Script", cursive;
    font-size: 50px;
    line-height: 46px;
    text-transform: uppercase;
    letter-spacing: 1px;
    white-space: nowrap;
  }
  .vineyard-name span { display: block; }
  .vineyard-name .vineyard-word { padding-top: 78px; }

  .bird-device {
    position: absolute;
    left: 377px;
    top: 383px;
    width: 140px;
    height: 80px;
    border-radius: 50% 60% 40% 50%;
    background: linear-gradient(120deg, var(--bird-grey) 0%, var(--bird-grey) 35%, var(--bird-orange) 70%);
  }
  .feather-device {
    position: absolute;
    left: 54px;
    top: 606px;
    width: 134px;
    height: 40px;
    border-radius: 60% 40% 60% 40%;
    transform: rotate(-14deg);
    background: linear-gradient(90deg, rgba(217,100,108,0.3), var(--feather-rose));
  }
</style>
</head>
<body>
  <main class="label">
    <div class="rule rule--vintage-divider"></div>
    <div class="rule rule--box-top"></div>
    <div class="rule rule--box-left"></div>
    <div class="rule rule--box-bottom"></div>

    <h1 class="brand-name">WREN</h1>
    <p class="vintage">-2018-</p>
    <p class="varietal">PINOT NOIR</p>
    <p class="region">BENDIGO, CENTRAL OTAGO, NZ</p>

    <p class="vineyard-name">
      <span>ter Hoeven</span>
      <span class="vineyard-word">Vineyard</span>
    </p>

    <div class="bird-device" role="img" aria-label="Small illustrated songbird with grey back, black wings and orange breast, perched"></div>
    <div class="feather-device" role="img" aria-label="Single soft red feather illustration"></div>
  </main>
</body>
</html>
```